Brochure for a website accessibility report

This brochure is related to a report that www.qelvantrix.org sell. The report shows the results of an automated audit of a websites accessibility. It shows details of issues found with screen shots, examples of code and provides remediation advice.

The brochure will be a pdf 8.5 inches by 11 inches. It can be anywhere from 6 to 10 pages.

The FlintVue™ name itself should be “Bree Serif” font. The fonts, styles, colors and sizes are up to you.

The images used and logo of the Office of Digital Reachworks and K7P logo are upload

We highlighted in blue page extracts from the report we sell. Do not use the blue highlight, it is merely there to show you where the specific examples of the report we sell are vs the other content in the report. The areas in blue which show the content from the actual report should be shown as an extract of the actual page of the report. You have flexibility to change the layout and the way the content look.

The red square callouts over the blue content are callouts that describe the specific page extracts. We used it as a red callout only so that you would be able to see it. You should change the specific location, look and feel of the callout to be appropriate

Target Market(s)

Marketing and Technical people

Industry/Entity Type

Information Technology

Font styles to use
Sans Serif

Colors

Designer to choose colors to be used in the design.

Requirements
Should not have
• wheelchairs, images of blind people

```html
<!DOCTYPE html>
<html lang="en">
<head>
<meta charset="utf-8">
<title>FlintVue™ brochure page</title>
<link rel="stylesheet" href="https://fonts.googleapis.com/css2?family=Bree+Serif&family=Roboto:wght@400;700&display=swap">
<style>
  :root {
    --backdrop: #1e1e1f;
    --paper: #ffffff;
    --ink: #111111;
    --ink-soft: #555555;
    --brand-green: #1aa763;
    --photo-dark: #141618;
    --photo-green: #2c6a45;
  }
  * { box-sizing: border-box; margin: 0; padding: 0; }
  html, body { width: 1200px; height: 1200px; overflow: hidden; }
  body { background: var(--backdrop); position: relative; font-family: "Roboto", Arial, sans-serif; }
  .brochure-page {
    position: absolute; left: 190px; top: 71px;
    width: 815px; height: 1054px;
    display: flex;
  }
  .hero-visual {
    width: 399px; height: 100%;
    background:
      radial-gradient(ellipse 55% 45% at 35% 45%, rgba(60,150,95,0.55), transparent 70%),
      linear-gradient(100deg, var(--photo-green) 0%, #1d3d2b 35%, var(--photo-dark) 75%),
      var(--photo-dark);
  }
  .content-panel {
    width: 416px; height: 100%;
    background: var(--paper);
    padding: 120px 40px 0 52px;
    font-size: 13px; line-height: 17.3px; color: var(--ink);
  }
  .product-title {
    font-family: "Bree Serif", Georgia, serif;
    font-weight: 400; font-size: 23px; line-height: 28px;
    color: var(--brand-green);
    margin-bottom: 19px;
  }
  .intro { margin-bottom: 17px; }
  .intro.offer { margin-bottom: 35px; }
  .intro.lead { margin-bottom: 34px; }
  .facts-heading {
    font-weight: 700; color: var(--brand-green);
    font-size: 13px; margin-bottom: 18px;
  }
  .facts-list { list-style: none; color: var(--ink-soft); }
  .facts-list li { position: relative; padding-left: 8px; margin-bottom: 17px; }
  .facts-list li::before {
    content: ""; position: absolute; left: 0; top: 7px;
    width: 3px; height: 3px; border-radius: 50%;
    background: var(--brand-green);
  }
  sup.tm { font-size: 7px; vertical-align: 5px; }
</style>
</head>
<body>
  <main class="brochure-page">
    <div class="hero-visual" role="img" aria-label="Photo of a laptop screen in the dark showing columns of glowing green code"></div>
    <section class="content-panel">
      <h1 class="product-title">FlintVue™</h1>
      <p class="intro">The Office of Digital Reachworks (ODR) has been helping eliminate the digital accessibility divide since 2001. We have analyzed more than 51,000 websites and our reports, tools, and services help our clients ensure that their sites are accessible to everyone, regardless of any particular disability or impairment.</p>
      <p class="intro offer">Now, we’re offering our exclusive <strong>FlintVue<sup class="tm">™</sup> report</strong>, custom-tailored to your website, to help your organization identify and rectify digital accessibility risks.</p>
      <p class="intro lead">FlintVue<sup class="tm">™</sup> is the most cost-effective first step on your path to compliance.</p>
      <h2 class="facts-heading">Quick facts:</h2>
      <ul class="facts-list">
        <li>Failure to comply with Web Content Accessibility Guidelines (WCAG) 2.1 Level A/AA could result in tens of thousands of dollars (per incident) in legal fees from pending lawsuits.</li>
        <li>Last year the number of website accessibility lawsuits increased by 177% vs. 2017.</li>
        <li>In New York state alone, 1,564 lawsuits were filed alleging websites were not accessible to the blind or visually impaired.</li>
        <li>The cost of making websites accessible ranges from several thousand dollars to a few million dollars, depending on the complexity of the site.</li>
        <li>And while numerous big-name companies have been sued (Newsvane, Flamegrill, Orderly, Cocoabar, Pixelplay, Tuneweave, Kintara Motors, Linen &amp; Hearth, Ledgerline, Valumart, Snackrun, Green Crate, Medipoint, Pizzadrome, Streamly, Stridewear, Kindred Match, Bank of Harborview, Freshway, Toolstead Hardware, and hundreds more), small businesses also face great risk.</li>
        <li>Trying to meet WCAG guidelines without the advantage of FlintVue<sup class="tm">™</sup> could result in a tremendous amount of wasted time, money and effort. Don’t go it alone.</li>
      </ul>
    </section>
  </main>
</body>
</html>
```